Disability provider requiring digital flyer to promote services

My company works within the Disability sector (KTAP registered provider), currently operating in Sydney, Australia.
I require a digital brochure which lists our services and gives potential customers a quick look into what we do with a single glance.
Undecided whether this digital flyer is to be single or double sided, happy to consult with an experienced designer in this regard.
I prefer minimalist designs (which may be an issue for someone trying to convey information, I'm not sure), and possibly someone who can work with out watercolor logo.
Services include:
-Supported Independent Living
-Specialist Disability Accommodation
-Individualised Living Options Stage 1 & 2
-Home Modifications
-Occupational Therapy
-Support Coordination Levels 1 & 2
-Short Term Accommodation - STA Respite
-Drop In Supports
-Community Access
Disability

```html
<!DOCTYPE html>
<html lang="en">
<head>
<meta charset="utf-8">
<title>Clearview Healthcare – Services Flyer</title>
<link rel="stylesheet" href="https://fonts.googleapis.com/css2?family=Bebas+Neue&family=Poppins:wght@400;500;600;700;800&display=swap">
<style>
:root{
  --stage:#e6e9ec;
  --paper:#ffffff;
  --teal:#3fbfa9;
  --blue:#2a6fc0;
  --ink:#1f1f24;
  --body:#4f4f57;
  --pink:#e27bd8;
  --band:#f8d9f1;
  --magenta:#d23fbf;
  --badge:#6a2f8a;
  --cyan:#1fa9e6;
  --photo-a:#b9c9a4;
  --photo-b:#e9eef0;
}
*{margin:0;padding:0;box-sizing:border-box}
html,body{width:1200px;height:2400px;overflow:hidden}
body{background:var(--stage);font-family:"Poppins",sans-serif;position:relative}
.flyer{position:absolute;left:0;top:351px;width:1200px;height:1698px;background:var(--paper);overflow:hidden;box-shadow:0 6px 24px rgba(0,0,0,.12)}
.flyer > *{position:absolute}
.photo{left:0;top:480px;width:900px;height:1218px;
  background:linear-gradient(90deg,var(--photo-a) 0%,#cfdcc0 40%,var(--photo-b) 70%,rgba(255,255,255,0) 100%),
             linear-gradient(180deg,#eef2ee 0%,var(--photo-a) 100%)}
.photo::after{content:"";position:absolute;inset:0;background:linear-gradient(90deg,rgba(255,255,255,0) 55%,#fff 100%)}
.brand{left:74px;top:150px;display:flex;align-items:center;gap:12px;font-weight:600;font-size:26px;line-height:1.15;color:var(--teal)}
.brand-dot{width:22px;height:22px;border-radius:50%;background:var(--teal);flex:none}
.kicker{left:346px;top:76px;font-family:"Bebas Neue",sans-serif;font-size:100px;line-height:1;color:var(--teal);letter-spacing:1px}
.headline{left:342px;top:160px;font-weight:800;font-size:118px;line-height:104px;color:var(--blue);letter-spacing:1px}
.tagline{left:346px;top:400px;font-weight:600;font-size:36px;line-height:44px;color:var(--ink)}
.intro-band{left:0;top:511px;width:1200px;height:168px;background:linear-gradient(90deg,var(--band) 0%,#fbe6f6 60%,#fdf1fb 100%);opacity:.92}
.intro{left:348px;top:555px;width:740px;font-size:20.5px;line-height:24.5px;color:var(--body)}
.services-title{left:577px;top:700px;font-weight:700;font-size:40px;color:var(--ink)}
.services-title .accent{color:var(--pink)}
.services{left:588px;top:764px;list-style:none}
.services li{display:flex;align-items:center;gap:22px;font-weight:500;font-size:23px;line-height:36.9px;color:var(--ink)}
.services svg{width:20px;height:20px;flex:none}
.badge{left:880px;top:1100px;width:196px;height:196px;border-radius:50%;background:var(--badge)}
.hours{left:827px;top:1327px;color:var(--ink);font-size:30px;line-height:31px}
.hours strong{display:block;font-weight:700;font-size:28px}
.cta{left:826px;top:1440px;font-weight:700;font-size:48px;color:var(--blue)}
.phone{left:826px;top:1502px;display:flex;align-items:center;gap:14px;font-weight:700;font-size:33px;color:var(--ink)}
.phone svg{width:38px;height:38px}
.web-bar{left:475px;top:1561px;width:725px;height:60px;background:var(--magenta);color:#fff;font-weight:700;font-size:28px;line-height:60px;text-align:right;padding-right:60px}
</style>
</head>
<body>
<main class="flyer">
  <div class="photo" role="img" aria-label="Smiling carer in white standing behind an older woman seated in a wheelchair in a sunny park"></div>

  <div class="brand"><span class="brand-dot"></span><span>Clearview<br>Healthcare</span></div>

  <div class="kicker">CLEARVIEW FOR AN</div>
  <h1 class="headline">EMPOWERED<br>FUTURE</h1>
  <p class="tagline">Works within the Disability sector,<br>currently operating in Sydney, Australia.</p>

  <div class="intro-band"></div>
  <p class="intro">Clearview Healthcare is a Sydney based disability support services<br>provider. Focusing on intellectual, physical &amp; sensory disabilities<br>including mental health within the Greater Sydney region, we strive to<br>assist our participants in leading an independent and fulfilling life.</p>

  <h2 class="services-title"><span class="accent">Services</span> We Provide</h2>
  <ul class="services">
    <li><svg viewBox="0 0 20 20"><circle cx="10" cy="10" r="10" fill="#1fa9e6"/><path d="M5.5 10.2l3 3 6-6" stroke="#fff" stroke-width="2.4" fill="none"/></svg>Supported Independent Living</li>
    <li><svg viewBox="0 0 20 20"><circle cx="10" cy="10" r="10" fill="#1fa9e6"/><path d="M5.5 10.2l3 3 6-6" stroke="#fff" stroke-width="2.4" fill="none"/></svg>Specialist Disability Accommodation</li>
    <li><svg viewBox="0 0 20 20"><circle cx="10" cy="10" r="10" fill="#1fa9e6"/><path d="M5.5 10.2l3 3 6-6" stroke="#fff" stroke-width="2.4" fill="none"/></svg>Individualised Living Options Stage 1 &amp; 2</li>
    <li><svg viewBox="0 0 20 20"><circle cx="10" cy="10" r="10" fill="#1fa9e6"/><path d="M5.5 10.2l3 3 6-6" stroke="#fff" stroke-width="2.4" fill="none"/></svg>Home Modifications</li>
    <li><svg viewBox="0 0 20 20"><circle cx="10" cy="10" r="10" fill="#1fa9e6"/><path d="M5.5 10.2l3 3 6-6" stroke="#fff" stroke-width="2.4" fill="none"/></svg>Occupational Therapy</li>
    <li><svg viewBox="0 0 20 20"><circle cx="10" cy="10" r="10" fill="#1fa9e6"/><path d="M5.5 10.2l3 3 6-6" stroke="#fff" stroke-width="2.4" fill="none"/></svg>Support Coordination Levels 1 &amp; 2</li>
    <li><svg viewBox="0 0 20 20"><circle cx="10" cy="10" r="10" fill="#1fa9e6"/><path d="M5.5 10.2l3 3 6-6" stroke="#fff" stroke-width="2.4" fill="none"/></svg>Short Term Accommodation - STA Respite</li>
    <li><svg viewBox="0 0 20 20"><circle cx="10" cy="10" r="10" fill="#1fa9e6"/><path d="M5.5 10.2l3 3 6-6" stroke="#fff" stroke-width="2.4" fill="none"/></svg>Drop In Supports</li>
    <li><svg viewBox="0 0 20 20"><circle cx="10" cy="10" r="10" fill="#1fa9e6"/><path d="M5.5 10.2l3 3 6-6" stroke="#fff" stroke-width="2.4" fill="none"/></svg>Community Access</li>
  </ul>

  <div class="badge" role="img" aria-label="Registered provider certification badge"></div>

  <p class="hours"><strong>OPERATING HOURS</strong>9AM To 5PM<br>Monday to Friday</p>
  <p class="cta">Call Us Now!</p>
  <p class="phone"><svg viewBox="0 0 38 38"><circle cx="19" cy="19" r="19" fill="var(--cyan)"/><path d="M13 10c1-1 2.5-1 3.2.2l1.6 2.8c.5.9.2 2-.6 2.6l-1.3 1c.9 2.2 2.7 4 4.9 4.9l1-1.3c.6-.8 1.7-1.1 2.6-.6l2.8 1.6c1.2.7 1.2 2.2.2 3.2l-1.3 1.3c-1.4 1.4-3.6 1.7-5.4.7-4.3-2.3-7.8-5.8-10.1-10.1-1-1.8-.7-4 .7-5.4z" fill="#fff"/></svg>+61 0491 570 156</p>

  <div class="web-bar">www.clearviewhealthcare.com.au</div>
</main>
</body>
</html>
```